Jolly Paws Business Card Update

I have a business card which I love. I want to keep the same logo, colours, font and style. I want to upgrade the scripting and remove some elements and add others.
On the front side under Services - remove the existing wording and insert - Providing individual coaching strategies to create happy, healthy and social canine companions
Under Denise Carvell amend the current wording to read: Qualified in Dog Behavioural Training, Natural Animal Healthcare and Animal Health Science
On the reverse side to remove the web address.

```html
<!DOCTYPE html>
<html lang="en">
<head>
<meta charset="utf-8">
<title>Jolly Paws Business Card</title>
<link href="https://fonts.googleapis.com/css2?family=Oxygen:wght@400;700&family=Arimo:wght@400;700&display=swap" rel="stylesheet">
<style>
  :root {
    --page-bg: #d8d1c9;
    --card-bg: #efedeb;
    --navy: #2c3a80;
    --red: #c0202d;
    --red-dark: #7e1c22;
    --blue: #2753b0;
    --teal: #2b93b3;
    --cream: #f4ecd6;
    --white-text: #f6f3f3;
    --label-grey: #dcdde6;
    --ink: #111111;
  }
  * { margin: 0; padding: 0; box-sizing: border-box; }
  html, body {
    width: 1200px;
    height: 1054px;
    overflow: hidden;
    background: var(--page-bg);
  }
  .card {
    position: absolute;
    left: 60px;
    top: 201px;
    width: 1080px;
    height: 652px;
    background: var(--card-bg);
    border-radius: 22px;
    overflow: hidden;
    box-shadow: 0 10px 30px rgba(0,0,0,0.12);
  }
  .name {
    position: absolute;
    left: 38px;
    top: 68px;
    font-family: "Oxygen", sans-serif;
    font-weight: 700;
    font-size: 42px;
    color: var(--navy);
    letter-spacing: 0.2px;
  }
  .qualifications {
    position: absolute;
    left: 38px;
    top: 122px;
    font-family: "Oxygen", sans-serif;
    font-size: 23px;
    line-height: 34px;
    color: var(--navy);
  }
  .contact-band {
    position: absolute;
    left: 0;
    top: 236px;
    width: 100%;
    height: 116px;
    background: linear-gradient(90deg, var(--red-dark) 0%, #a11f29 35%, var(--red) 65%, var(--red-dark) 82%, var(--red-dark) 100%);
  }
  .contact-line {
    position: absolute;
    left: 38px;
    display: flex;
    align-items: center;
    font-family: "Oxygen", sans-serif;
    font-size: 25px;
    color: var(--white-text);
  }
  .contact-line.first { top: 256px; }
  .contact-line.second { top: 295px; }
  .contact-line svg { margin-right: 16px; flex: none; }
  .contact-line .email { margin-left: 26px; display: flex; align-items: center; }
  .services-band {
    position: absolute;
    left: 0;
    top: 352px;
    width: 100%;
    height: 178px;
    background: linear-gradient(90deg, #2a4aa6 0%, var(--blue) 45%, #2b75b4 75%, var(--teal) 100%);
  }
  .services-title {
    position: absolute;
    left: 38px;
    top: 376px;
    font-family: "Arimo", sans-serif;
    font-weight: 700;
    font-size: 31px;
    color: var(--label-grey);
  }
  .services-text {
    position: absolute;
    left: 38px;
    top: 425px;
    font-family: "Arimo", sans-serif;
    font-size: 25px;
    line-height: 32px;
    color: var(--label-grey);
  }
  .brand-mark {
    position: absolute;
    left: 667px;
    top: 174px;
    width: 378px;
    height: 378px;
  }
  .tagline {
    position: absolute;
    left: 38px;
    top: 582px;
    font-family: "Arimo", sans-serif;
    font-size: 26px;
    color: var(--ink);
  }
</style>
</head>
<body>
  <div class="card">
    <div class="name">Denise Carvell</div>
    <div class="qualifications">
      Qualified in Dog Behavioural Training,<br>
      Natural Animal Healthcare &amp; Animal Health Science
    </div>

    <div class="contact-band"></div>
    <div class="contact-line first">
      <svg width="16" height="26" viewBox="0 0 16 26" aria-hidden="true">
        <rect x="1.5" y="1.5" width="13" height="23" rx="2" fill="none" stroke="var(--white-text)" stroke-width="2"/>
        <rect x="4" y="5" width="8" height="7" fill="var(--white-text)"/>
        <circle cx="5" cy="16" r="1.2" fill="var(--white-text)"/><circle cx="8" cy="16" r="1.2" fill="var(--white-text)"/><circle cx="11" cy="16" r="1.2" fill="var(--white-text)"/>
        <circle cx="5" cy="20" r="1.2" fill="var(--white-text)"/><circle cx="8" cy="20" r="1.2" fill="var(--white-text)"/><circle cx="11" cy="20" r="1.2" fill="var(--white-text)"/>
      </svg>
      <span>0400 628 417</span>
      <span class="email">
        <svg width="24" height="18" viewBox="0 0 24 18" aria-hidden="true">
          <rect x="0" y="1" width="24" height="16" rx="1.5" fill="var(--white-text)"/>
          <path d="M1 2 L12 10 L23 2" fill="none" stroke="#a11f29" stroke-width="2"/>
        </svg>
        jollypaws1@mail.com
      </span>
    </div>
    <div class="contact-line second">
      <svg width="18" height="18" viewBox="0 0 18 18" aria-hidden="true">
        <circle cx="9" cy="9" r="8" fill="none" stroke="var(--white-text)" stroke-width="1.6"/>
        <ellipse cx="9" cy="9" rx="3.5" ry="8" fill="none" stroke="var(--white-text)" stroke-width="1.4"/>
        <line x1="1" y1="9" x2="17" y2="9" stroke="var(--white-text)" stroke-width="1.4"/>
        <line x1="2.5" y1="5" x2="15.5" y2="5" stroke="var(--white-text)" stroke-width="1.2"/>
        <line x1="2.5" y1="13" x2="15.5" y2="13" stroke="var(--white-text)" stroke-width="1.2"/>
      </svg>
      <span>www.jollypaws1.com</span>
    </div>

    <div class="services-band"></div>
    <div class="services-title">SERVICES</div>
    <div class="services-text">
      Providing individual coaching strategies to create<br>
      happy, healthy and social canine companions
    </div>

    <svg class="brand-mark" viewBox="0 0 378 378" aria-label="Jolly Paws">
      <circle cx="189" cy="189" r="176" fill="var(--cream)" stroke="var(--red)" stroke-width="24"/>
      <text x="189" y="203" text-anchor="middle" font-family="Oxygen, sans-serif" font-weight="700" font-size="42" fill="var(--navy)">Jolly Paws</text>
    </svg>

    <div class="tagline">Promoting communication and connection between dogs and their families</div>
  </div>
</body>
</html>
```